BLUE & ORANGE BALM TOPICAL BOX + LABELS TO MATCH

Hello ! I hope you're up to helping with my designs again. I appreciate all your help.
I have two topicals needing redesign.
Box + Label , once the box is together, we can slap the labels together easy.
I have CBD version and THC version of both these balms, so well start w THC, then lay out the CBD. It should be eaay with few minor differences.
PLEASE USE only tHE SMALL BOX TEMPLATE,
Anyway, once the boxes are complete, I need to revise the label to match the boxes.
1.
ORANGE BALM :
(this box color I would like orange, like a jack-o-lantern (i uploaded our current label so you can match it)
KORVEN logo outlined in Gold (on LID)
(I uploaded a picture of what the oulined logo looks like)
THC SYMBOL
ORANGE BALM (GOLD) (on Front)
HIGHLY NUTRITIOUS POWERFUL THC RELIEF
net wt. 2 oz (56 g)
SIDE PANEL :
ORGANIC INGREDIENTS : Butyrospermum Parkii Butter (Shea Butter), Persia Gratissima (Avocado) Oil, Simmondsia chinesis (Gold Jojoba) Oil , Vitus Vinifera (Grape) Seed Oil, Arnica montana (Arnica) and Symphytum officinalis (Comfrey Leaf) macerated in Sunflower Oil, Calophyllum inophyllum (Tamanu) Oil, Nigella sativa (Black Seed) Oil, Locally Harvested Beeswax, THC CANNABIS EXTRACT, Pure Cannabigerol (CBG), Proprietary Blend of Therapeutic Essential Oils (including but not limited to : Yarrow , Celery Seed , Tea Tree , Lavender , Helichrysum, Pine Scotch, Rosemary, Geranium), Tocopherol (Vitamin E, antioxidant )
Color is a Natural Result of Chamomile Steam-Distillation and May Vary in Intensity. Consistency can also Vary. For Optimal Preservation, Keep in a Cool, Dark Place. Fatty Acids may Naturally Aggregate when Exposed to Temperature Extremes Forming Beads. To Fix This, Use a Hair Dryer to Melt them Back to a Smooth Consistency.
BACK PANEL :
WARNING: THIS PRODUCT IS FOR USE BY INDIVIDUALS 21 YEARS OF AGE OR OLDER OR BY REGISTERED QUALIFYING PATIENTS ONLY. IT IS ILLEGAL TO DRIVE A MOTOR VEHICLE WHILE UNDER THE INFLUENCE OF MARIJUANA.
(Outlined Box )::
WARNING: USE BY PREGNANT OR BREASTFEEDING WOMEN OR BY WOMEN PLANNING TO BECOME PREGNANT, MAY RESULT IN FETAL INJURY, PRETERM BIRTH, LOW BIRTHWEIGHT, OR DEVELOPMENTAL PROBLEMS FOR THE CHILD.
KEEP OUT OF REACH OF CHILDREN.
CENTRAL TOXIN RESPONSE BUREAU 1 800 555 0147
THE ACTUAL VALUE OF CANNABINOIDS MAY VARY FROM THE REPORTED VALUE BY +/- 10%
ACTIVATION TIME : 10 - 60 MINUTES
MADE IN A MARIJUANA FACILITY
PACKAGED BY
MIRABEL’S LUSH Co.
QX-R-748315
www.LUSHTARTS.info
2.
BLUE BALM
white box
KORVEN Gold out line, red w blue leaf
FRONT PANEL :
BLUE BALM (blue)
net wt. 2 oz (56 g)
Ingredients : Butyrospermum Parkii Butter (Shea Butter), Aloe Barbadensis (Aloe Vera) Leaf Extract, Coco Nucifera (Coconut) Oil, THC CANNABIS EXTRACT, Cannabis Sativa Seed Oil, Pure Cannabidol (Hemp Extract), Prunes Armeniaca (Apricot) Kernal Oil, Hydrogenated Vegetable (Soybean) Oil, Prunus Amygdalus Dulcis (Sweet Almond Oil), Vitus Vinifera (Grape) Seed Oil, Macadamia Ternifolia Seed Oil, Daucus Carota (Carrot) Seed Oil, Proprietary Blend of Therapeutic Essential Oils (including but not limited to : Lavender, Chamomile), Tocopherol (Vitamin E, antioxidant)

```html
<!DOCTYPE html>
<html lang="en">
<head>
<meta charset="utf-8">
<title>Korven Orange Balm – Box Dieline</title>
<link href="https://fonts.googleapis.com/css2?family=Oswald:wght@400;500;700&family=Roboto+Condensed:wght@300;400;700&family=Jost:wght@400&family=Montserrat:wght@500&display=swap" rel="stylesheet">
<style>
  :root{
    --exterior:#F26B22;
    --interior:#F9DC0A;
    --text-gold:#FCC12F;
    --brand-red:#E3262A;
    --brand-green:#1E8A3E;
    --accent-yellow:#EEE71F;
    --cut:#2b2b2b;
    --fold:#9bc77a;
    --ink:#231F20;
  }
  html,body{margin:0;padding:0;width:1200px;height:609px;overflow:hidden;background:#fff;}
  .sheet{display:block;width:1200px;height:609px;}
  .cut-line{fill:none;stroke:var(--cut);stroke-width:1.4;}
  .fold-line{fill:none;stroke:var(--fold);stroke-width:1;}
  .brand-name{font-family:'Oswald',sans-serif;font-weight:700;fill:var(--brand-red);}
  .tagline{font-family:'Montserrat',sans-serif;font-weight:500;fill:var(--text-gold);letter-spacing:9px;}
  .product-name{font-family:'Oswald',sans-serif;font-weight:400;}
  .panel-copy{font-family:'Roboto Condensed',sans-serif;font-weight:300;fill:var(--text-gold);}
  .panel-copy-bold{font-family:'Roboto Condensed',sans-serif;font-weight:700;fill:var(--text-gold);}
  .spec-label{font-family:'Jost',sans-serif;fill:var(--ink);}
  .icon-ring{fill:none;stroke:var(--text-gold);stroke-width:2;}
</style>
</head>
<body>
<svg class="sheet" viewBox="0 0 2560 1300" xmlns="http://www.w3.org/2000/svg">
  <defs>
    <linearGradient id="gold" x1="0" y1="0" x2="1" y2="0">
      <stop offset="0" stop-color="#C19A48"/>
      <stop offset="0.5" stop-color="#EBCB78"/>
      <stop offset="1" stop-color="#B88A3A"/>
    </linearGradient>
    <path id="box-outline" d="M347,320 V285 Q347,222 410,222 H585 Q647,222 647,285 V310 L650,450 H882 L920,545 V585 H1195 L1272,597 V848 L1198,865 V1165 Q1198,1232 1130,1232 H965 Q897,1232 897,1165 V1005 H662 L640,895 L622,870 H370 L352,895 L330,1005 H88 L72,870 V555 L112,450 H347 Z"/>
    <g id="box-cuts">
      <path class="cut-line" d="M362,323 V290 Q362,237 415,237 H580 Q632,237 632,290 V323"/>
      <path class="cut-line" d="M87,600 V575 L120,465 H340 L345,590 L358,600"/>
      <path class="cut-line" d="M635,600 L650,590 L652,465 H870 L905,575 V600"/>
      <path class="cut-line" d="M87,857 V880 L103,990 H340 L358,870 V857"/>
      <path class="cut-line" d="M635,857 V870 L660,990 H890 L895,870 L908,857"/>
      <path class="cut-line" d="M908,1133 V1170 Q908,1220 960,1220 H1135 Q1185,1220 1185,1170 V1133"/>
      <path class="cut-line" d="M1185,600 L1257,615 V840 L1185,857"/>
      <path class="cut-line" d="M358,323 H398 M635,323 H595 M908,1133 H948 M1185,1133 H1145"/>
      <path class="fold-line" d="M87,600 H1185 M87,857 H1185 M358,600 V857 M635,600 V857 M908,600 V857 M1185,600 V857 M358,323 H635 M908,1133 H1185 M358,323 V600 M635,323 V600 M908,857 V1133 M1185,857 V1133"/>
    </g>
  </defs>

  <!-- Exterior print side -->
  <g class="box-exterior">
    <use href="#box-outline" fill="var(--exterior)"/>
    <use href="#box-cuts"/>

    <!-- Lid -->
    <g class="lid-panel" text-anchor="middle">
      <text class="brand-name" x="497" y="447" font-size="78">KORVEN</text>
      <text class="tagline" x="500" y="474" font-size="18">BOTANIC</text>
      <text class="product-name" x="497" y="535" font-size="68" fill="url(#gold)" textLength="238" lengthAdjust="spacingAndGlyphs">ORANGE BALM</text>
    </g>

    <!-- Top dust flap message -->
    <g class="flap-message panel-copy" font-size="12.5" text-anchor="middle">
      <text transform="translate(716,532) rotate(-90)">You are truly at the heart</text>
      <text transform="translate(730,532) rotate(-90)">of what we do and we</text>
      <text transform="translate(744,532) rotate(-90)">are so grateful to share</text>
      <text transform="translate(758,532) rotate(-90)">our passion with you. We</text>
      <text transform="translate(772,532) rotate(-90)">hope our product can</text>
      <text transform="translate(786,532) rotate(-90)">make a difference in</text>
      <text transform="translate(800,532) rotate(-90)">your life.</text>
      <text transform="translate(826,532) rotate(-90)" font-family="Oswald,sans-serif" font-weight="400" font-size="18" letter-spacing="1">KORVEN</text>
      <path d="M820,574 c-7,-6 -7,-12 -2,-12 c2,0 2,2 2,3 c0,-1 0,-3 2,-3 c5,0 5,6 -2,12z" fill="var(--text-gold)"/>
    </g>

    <!-- Left side panel -->
    <g class="benefits-panel">
      <g role="img" aria-label="Four round benefit icons: organic ingredients, high potency, powerful relief, natural healing">
        <circle class="icon-ring" cx="131" cy="652" r="25"/>
        <circle class="icon-ring" cx="192" cy="652" r="25"/>
        <circle class="icon-ring" cx="253" cy="652" r="25"/>
        <circle class="icon-ring" cx="315" cy="652" r="25"/>
      </g>
      <g class="panel-copy" font-size="12">
        <text x="107" y="710" textLength="233" lengthAdjust="spacing">KORVEN ORANGE BALM is a sophisticated synergy</text>
        <text x="107" y="725.5" textLength="233" lengthAdjust="spacing">of botanial-rich actives embraced with natural and</text>
        <text x="107" y="741" textLength="233" lengthAdjust="spacing">organic oils overflowing with high-content anti-</text>
        <text x="107" y="756.5" textLength="233" lengthAdjust="spacing">oxidants and phytonutrients and supercharged</text>
        <text x="107" y="772" textLength="233" lengthAdjust="spacing">with THC. The intrinsic nature of this balm brings</text>
        <text x="107" y="787.5" textLength="233" lengthAdjust="spacing">forth much needed relief and healing to the areas</text>
        <text x="107" y="803" textLength="233" lengthAdjust="spacing">where you need it the most. The intelligence of this</text>
        <text x="107" y="818.5" textLength="233" lengthAdjust="spacing">alchemized blend is characterized by its powerful,</text>
        <text x="107" y="834">repairing and deeply soothing comforts.</text>
      </g>
    </g>

    <!-- Front panel -->
    <g class="front-panel" text-anchor="middle">
      <circle class="compliance-mark" cx="594" cy="634" r="20" fill="var(--brand-green)" role="img" aria-label="Compliance mark placeholder"/>
      <text class="brand-name" x="497" y="722" font-size="78">KORVEN</text>
      <text class="tagline" x="500" y="749" font-size="18">BOTANIC</text>
      <text class="product-name" x="497" y="810" font-size="68" fill="url(#gold)" textLength="238" lengthAdjust="spacingAndGlyphs">ORANGE BALM</text>
      <text class="panel-copy" x="497" y="834" font-size="11">net wt. 2 oz (56 g)</text>
    </g>

    <!-- Ingredients panel -->
    <g class="ingredients-panel panel-copy">
      <g font-size="10.6">
        <text x="655" y="629" textLength="233" lengthAdjust="spacing">ORGANIC INGREDIENTS : Butyrospermum Parkii Butter</text>
        <text x="655" y="641" textLength="233" lengthAdjust="spacing">(Shea Butter), Persia Gratissima (Avocado) Oil, Simmondsia</text>
        <text x="655" y="653" textLength="233" lengthAdjust="spacing">chinesis (Gold Jojoba) Oil, Vitus Vinifera (Grape) Seed Oil,</text>
        <text x="655" y="665" textLength="233" lengthAdjust="spacing">Arnica montana (Arnica) and Symphytum officinalis</text>
        <text x="655" y="677" textLength="233" lengthAdjust="spacing">(Comfrey Leaf) macerated in Sunflower Oil, Calophyllum</text>
        <text x="655" y="689" textLength="233" lengthAdjust="spacing">inophyllum (Tamanu) Oil, Nigella sativa (Black Seed) Oil,</text>
        <text x="655" y="701" textLength="233" lengthAdjust="spacing">Locally Harvested Beeswax, THC CANNABIS EXTRACT, Pure</text>
        <text x="655" y="713" textLength="233" lengthAdjust="spacing">Cannabigerol (CBG), Proprietary Blend of Therapeutic</text>
        <text x="655" y="725" textLength="233" lengthAdjust="spacing">Essential Oils (including but not limited to : Yarrow, Celery</text>
        <text x="655" y="737" textLength="233" lengthAdjust="spacing">Seed, Tea Tree, Lavender, Helichrysum, Pine Scotch,</text>
        <text x="655" y="749">Rosemary, Geranium), Tocopherol (Vitamin E, antioxidant )</text>
      </g>
      <g font-size="7.6">
        <text x="655" y="770" textLength="233" lengthAdjust="spacing">Color is a Natural result of the Phytonutrients within the Formula and May</text>
        <text x="655" y="781" textLength="233" lengthAdjust="spacing">Vary in Intensity. Consistency may also Vary. For Optimal Preservation,</text>
        <text x="655" y="792" textLength="233" lengthAdjust="spacing">Keep in a Cool, Dark Place. Fatty Acids may Naturally Aggregate when</text>
        <text x="655" y="803" textLength="233" lengthAdjust="spacing">Exposed to Temperature Extremes Forming Beads. To Fix This, Use a Hair</text>
        <text x="655" y="814" textLength="233" lengthAdjust="spacing">Dryer to Melt them Back to a Smooth Consistency. For Best Results, Apply</text>
        <text x="655" y="825" textLength="233" lengthAdjust="spacing">to Skin after a warm wash. Botanical oils and Healing compounds are better</text>
        <text x="655" y="836">able to lock into the dermis when the pores are clean, warm and open.</text>
      </g>
    </g>

    <!-- Back panel -->
    <g class="back-panel" text-anchor="middle">
      <g class="panel-copy-bold" font-size="10.5">
        <text x="1047" y="629" textLength="232" lengthAdjust="spacingAndGlyphs">POTENT RELIEF • ULTRA HEALING • NON PSYCHOACTIVE</text>
        <text x="1047" y="641">SMALL BATCH • PLANT BASED • HIGH THC FORMULA</text>
      </g>
      <g class="panel-copy" font-size="8.2">
        <text x="1047" y="657" textLength="232" lengthAdjust="spacing">THIS PRODUCT IS FOR USE BY INDIVIDUALS 21 YEARS OF AGE OR</text>
        <text x="1047" y="667" textLength="232" lengthAdjust="spacing">OLDER OR BY REGISTERED QUALIFYING PATIENTS ONLY. IT IS</text>
        <text x="1047" y="677" textLength="232" lengthAdjust="spacing">ILLEGAL TO DRIVE A MOTOR VEHICLE WHILE UNDER THE INFLUENCE</text>
        <text x="1047" y="687">OF MARIJUANA. ACTIVATION TIME : 30 MINUTES</text>
        <text x="1047" y="702">KEEP OUT OF REACH OF CHILDREN.</text>
        <text x="1047" y="711">CENTRAL TOXIN RESPONSE BUREAU 1 800 555 0147</text>
      </g>
      <rect x="931" y="722" width="232" height="48" fill="none" stroke="var(--text-gold)" stroke-width="1.5"/>
      <g class="panel-copy" font-size="8">
        <text x="1047" y="733" textLength="218" lengthAdjust="spacing">WARNING: USE BY PREGNANT OR BREASTFEEDING WOMEN OR</text>
        <text x="1047" y="743" textLength="218" lengthAdjust="spacing">BY WOMEN PLANNING TO BECOME PREGNANT, MAY RESULT IN</text>
        <text x="1047" y="753" textLength="218" lengthAdjust="spacing">FETAL INJURY, PRETERM BIRTH, LOW BIRTHWEIGHT, OR</text>
        <text x="1047" y="763">DEVELOPMENTAL PROBLEMS FOR THE CHILD.</text>
        <text x="1047" y="786">THE ACTUAL VALUE OF CANNABINOIDS MAY</text>
        <text x="1047" y="795">VARY FROM THE REPORTED VALUE BY +/-10%</text>
        <text x="1047" y="804">MADE IN A MARIJUANA FACILITY</text>
        <text x="1047" y="813">PACKAGED BY : MIRABEL'S LUSH QX R 748315</text>
      </g>
      <g class="panel-copy" font-size="7.6">
        <text x="1047" y="828">These Statements have not been evaluated by the FDA. This product is</text>
        <text x="1047" y="837">not intended to diagnose, treat, cure, or prevent any disease or condition.</text>
      </g>
    </g>
  </g>

  <!-- Colour specifications -->
  <g class="color-specs">
    <rect x="992" y="126" width="55" height="55" fill="var(--interior)"/>
    <text class="spec-label" x="1060" y="144" font-size="17">Box interior color:</text>
    <text class="spec-label" x="1060" y="162" font-size="14">CMYK: 2,11,100,0</text>
    <text class="spec-label" x="1060" y="176" font-size="10">(SAME AS HONEY BOX)</text>

    <rect x="992" y="199" width="55" height="55" fill="var(--exterior)"/>
    <text class="spec-label" x="1060" y="223" font-size="17">Box exterior color:</text>
    <text class="spec-label" x="1060" y="241" font-size="14">CMYK: 0,74,100,0</text>

    <rect x="992" y="276" width="55" height="55" fill="var(--text-gold)"/>
    <text class="spec-label" x="1060" y="300" font-size="17">Box Text color:</text>
    <text class="spec-label" x="1060" y="318" font-size="14">CMYK: 0,23,89,0</text>

    <g role="img" aria-label="Organic ingredients icon colour callout">
      <circle cx="1229" cy="303" r="35" fill="var(--exterior)"/>
      <circle cx="1229" cy="303" r="27" fill="none" stroke="var(--text-gold)" stroke-width="2"/>
      <path d="M1270,262 c-12,-10 -12,-20 -4,-20 c3,0 4,3 4,5 c0,-2 1,-5 4,-5 c8,0 8,10 -4,20z" fill="var(--accent-yellow)"/>
      <path d="M1272,255 L1287,282 M1222,303 H1275" stroke="var(--ink)" stroke-width="1.2" fill="none"/>
      <circle cx="1295" cy="303" r="20" fill="var(--accent-yellow)"/>
    </g>
    <text class="spec-label" x="1320" y="309" font-size="14">CMYK: 6, 0, 97, 0</text>

    <rect x="992" y="356" width="55" height="55" fill="url(#gold)"/>
    <g text-anchor="middle">
      <text class="product-name" x="1106" y="378" font-size="24" fill="url(#gold)">KORVEN</text>
      <text class="product-name" x="1106" y="403" font-size="20" fill="url(#gold)">ORANGE BALM</text>
      <text class="brand-name" x="1036" y="458" font-size="26">KORVEN</text>
    </g>
    <circle cx="1101" cy="432" r="10" fill="var(--brand-green)"/>
    <text class="spec-label" x="1116" y="437" font-size="14">CMYK: 88,24,96,11</text>
    <circle cx="1101" cy="459" r="10" fill="var(--brand-red)"/>
    <text class="spec-label" x="1116" y="464" font-size="14">CMYK: 0,99,100,0</text>
  </g>

  <!-- Interior print side -->
  <g class="box-interior" transform="translate(1225,0)">
    <use href="#box-outline" fill="var(--interior)"/>
    <use href="#box-cuts"/>
  </g>
  <rect x="1638" y="938" width="52" height="50" fill="var(--interior)"/>
  <text class="spec-label" x="1702" y="960" font-size="17">Box interior color:</text>
  <text class="spec-label" x="1702" y="977" font-size="14">CMYK: 2,11,100,0</text>
</svg>
</body>
</html>
```